Advanced Therapeutic Massage Therapist

I need a business card advertising my massage services as an advanced therapeutic massage therapist. I offer advanced therapeutic massage, swedish and deep tissue. I want to create a simple, professional and feminine card. I like bright colours and creativity.

I prefer a bold and experimental approach rather than something status-quo. A card to suggest therapeutic healing through dynamic massage. Motifs, shapes or layout which suggest movement and flow.
Updates

Target Market(s)

Everybody!

Industry/Entity Type

Health And Wellness

Contact Information for Business Card

The card should include:
My name, logo, services offered and my contact details.

Sláine Dunleavy
Massage Therapist

- Swedish - Deep Tissue - Advanced Therapeutic

Phone: (+353) 87 216 4093
Email: regenerate@slainedunleavy-example.com
Website: www.slainedunlevy-example.com

Font styles to use
Serif
Sans Serif
Decorative
Script

Colors

Designer to choose colors to be used in the design.

Requirements
Must have
• An example may contain something like this, yet concise:
• "Sláine Dunleavy
• Massage Therapist
• - Swedish - Deep Tissue - Advanced Therapeutic"
Nice to have
• This sentence is optional:
• Imagery such as a logo or symbol. I have attached a file containing a logo I had produced however the name is incorrect now as it is "Sláine" not "Nelly". It could be edited to change it to Sláine.
• I have sent the file as .psd .jpg. .pdf and .png
• I like when the card conveys energy, movement, pressure points, flow etc.
• I just like the designer to follow their own style and ideas. I like bright colours but must have a lot of a base colour to offset it. I really prefer them to follow their own inspiration. That is my preference.
Should not have
• Pine trees, non-native trees to Britain and Ireland, exotic flowers or animals that are not native to Britain and Ireland.
• I don't like brown as the background colour of the card.
• The cars shouldn't look like a wedding invitation i.e too many floral type designs.

```html
<!DOCTYPE html>
<html lang="en">
<head>
<meta charset="utf-8">
<title>Sláine Dunleavy – Massage Therapist Business Card</title>
<link rel="stylesheet" href="https://fonts.googleapis.com/css2?family=Great+Vibes&family=Quicksand:wght@400;500&display=swap">
<style>
  :root {
    --stage: #666666;
    --mint-light: #cdeee3;
    --mint: #a9e0d2;
    --mint-deep: #8fd3c3;
    --ink: #1f1f1f;
    --charcoal: #232323;
    --gold: #e0ae3c;
    --gold-deep: #b8862a;
    --white: #ffffff;
    --text-dark: #2b2b2b;
  }
  * { margin: 0; padding: 0; box-sizing: border-box; }
  html, body {
    width: 1200px; height: 550px; overflow: hidden;
    background: var(--stage);
  }
  .stage { position: relative; width: 1200px; height: 550px; }

  .card {
    position: absolute; top: 157px;
    width: 390px; height: 235px; overflow: hidden;
  }
  .card--front {
    left: 195px;
    background:
      radial-gradient(ellipse at 25% 30%, var(--mint-light) 0%, transparent 55%),
      radial-gradient(ellipse at 75% 75%, var(--mint-deep) 0%, transparent 60%),
      var(--mint);
  }
  .card--back { left: 614px; background: var(--charcoal); }

  .logo-mark {
    position: absolute; border-radius: 50%;
    display: flex; align-items: center; justify-content: center;
    background: radial-gradient(circle, var(--mint-light) 0%, var(--mint) 100%);
    border: 2px solid var(--gold);
  }
  .card--front .logo-mark { left: 139px; top: 43px; width: 112px; height: 112px; }
  .card--back .logo-mark { left: 46px; top: 35px; width: 128px; height: 128px; }
  .logo-mark__name {
    font-family: "Quicksand", sans-serif; font-weight: 500;
    font-size: 11px; color: var(--gold-deep); letter-spacing: 0.5px;
  }

  .name { font-family: "Great Vibes", cursive; font-weight: 400; line-height: 1; }
  .role, .services {
    font-family: "Quicksand", sans-serif; font-weight: 400;
    letter-spacing: 1px; line-height: 1;
  }

  .card--front .identity {
    position: absolute; left: 0; right: 0; top: 160px; text-align: center;
    color: var(--text-dark);
  }
  .card--front .name { font-size: 24px; }
  .card--front .role { font-size: 9.5px; margin-top: 1px; }
  .card--front .services { font-size: 8px; letter-spacing: 0.6px; margin-top: 8px; }

  .card--back .identity {
    position: absolute; right: 22px; top: 32px; text-align: center;
    color: var(--white);
  }
  .card--back .name { font-size: 26px; }
  .card--back .role { font-size: 10px; margin-top: 2px; }

  .wave { position: absolute; left: 0; top: 0; width: 390px; height: 235px; }

  .contact {
    position: absolute; right: 20px; top: 174px; list-style: none;
    font-family: "Quicksand", sans-serif; font-weight: 500;
    font-size: 10px; color: var(--ink); text-align: right;
  }
  .contact li {
    display: flex; align-items: center; justify-content: flex-end;
    gap: 7px; height: 17px; white-space: nowrap;
  }
  .contact svg { width: 9px; height: 9px; fill: var(--ink); flex: none; }
</style>
</head>
<body>
<main class="stage">

  <section class="card card--front">
    <div class="logo-mark" role="img" aria-label="Client logo mark">
      <span class="logo-mark__name">Sláine Dunleavy</span>
    </div>
    <div class="identity">
      <p class="name">Sláine Dunleavy</p>
      <p class="role">massage therapist</p>
      <p class="services">Swedish · Deep Tissue · Advanced Therapeutic</p>
    </div>
  </section>

  <section class="card card--back">
    <svg class="wave" viewBox="0 0 390 235" aria-hidden="true">
      <defs>
        <linearGradient id="goldSweep" x1="0" y1="0" x2="1" y2="0">
          <stop offset="0" stop-color="#d49a2e"/>
          <stop offset="0.5" stop-color="#f7d46a"/>
          <stop offset="1" stop-color="#f2c54c"/>
        </linearGradient>
        <linearGradient id="mintWash" x1="0" y1="0" x2="1" y2="1">
          <stop offset="0" stop-color="#bfe8dc"/>
          <stop offset="1" stop-color="#9fdccd"/>
        </linearGradient>
      </defs>
      <path d="M0,229 C70,233 150,222 215,188 C280,152 335,137 390,134 L390,235 L0,235 Z" fill="url(#mintWash)"/>
      <path d="M0,184 C70,194 150,198 215,168 C280,136 335,119 390,116 L390,124 C335,127 280,142 215,176 C150,210 70,205 0,193 Z" fill="url(#goldSweep)"/>
      <path d="M0,204 C60,210 130,213 190,198 C130,216 60,216 0,211 Z" fill="url(#goldSweep)"/>
    </svg>

    <div class="logo-mark" role="img" aria-label="Client logo mark">
      <span class="logo-mark__name">Sláine Dunleavy</span>
    </div>

    <div class="identity">
      <p class="name">Sláine Dunleavy</p>
      <p class="role">massage therapist</p>
    </div>

    <ul class="contact">
      <li>(+353) 87 216 4093
        <svg viewBox="0 0 10 10" aria-hidden="true"><path d="M1,4 C1,2 3,1.5 5,1.5 C7,1.5 9,2 9,4 L7,4.3 L6.6,3.2 L3.4,3.2 L3,4.3 Z M2,5 L8,5 L9,9 L1,9 Z"/></svg>
      </li>
      <li>slainedunleavy-example.com
        <svg viewBox="0 0 10 10" aria-hidden="true"><path d="M0.5,2 L9.5,2 L9.5,8.5 L0.5,8.5 Z M1.2,2.6 L5,5.6 L8.8,2.6 Z" fill-rule="evenodd"/></svg>
      </li>
      <li>slaine@slainedunleavy-example.com
        <svg viewBox="0 0 10 10" aria-hidden="true"><circle cx="5" cy="5" r="4.3" fill="none" stroke="#1f1f1f" stroke-width="1"/><ellipse cx="5" cy="5" rx="1.8" ry="4.3" fill="none" stroke="#1f1f1f" stroke-width="0.8"/><path d="M0.7,5 L9.3,5" stroke="#1f1f1f" stroke-width="0.8"/></svg>
      </li>
    </ul>
  </section>

</main>
</body>
</html>
```